Dwelvano - "Where Pest Control is Free for Life..." Please see pitch deck...

Project goal, that this is a reusable template, not a one-off card
Brand and design direction, follow the logo, use the brand palette (with a color swatch table), typography and layout guidance
The John Doe placeholder content as a clean field-by-field table (name, title, company, address, office, cell, fax, email, dwelvano.com)
Print specs, 3.5 × 2 in trim, 0.125 in bleed, 300 DPI, CMYK, crop marks
Deliverables, layered editable PSD (your primary ask) plus vector .AI/.EPS and a press-ready PDF/X-1a, with fonts packaged
What you'll provide (logo, colors, fonts)
Process and sign-off, concept first, then full file package on approval.
Populate every field with this John Doe placeholder data so we can see the layout fully built out. We will replace it per person.
Name John Doe
Title Title / Position
Company Dwelvano
Address 480 Cedar Avenue, Suite 210, Marlow Bay, FL 32999
Office (555) 201-4470
Cell (555) 201-4488
Fax (555) 201-4495
Email johndoe@dwelvano.com
Website dwelvano.com

We need the working, editable source files so we can update them ourselves, plus a ready-to-print export:
1. Photoshop (.PSD) — fully layered and editable, with each contact field on its own labeled text layer. This is the primary requested format.
2. Vector source — the press-standard editable format, Adobe Illustrator (.AI) and/or .EPS, since vector is preferred for crisp text and logos at print.
3. Print-ready PDF — press-quality (PDF/X-1a), CMYK, with bleed and crop marks, both sides.
4. Packaged fonts and links — include or list all fonts used, and package any linked assets so the files open correctly on our end.

Why both PSD and vector
The PSD covers our request directly and is easy for us to edit. Vector (.AI/.EPS) is what most commercial printers actually prefer for type and logos because it stays razor-sharp at any size. Providing both keeps us flexible no matter which printer we use. Have fun and keep it modern and cool the designer of the logo did a great job, see what you can do.

```html
<!DOCTYPE html>
<html lang="en">
<head>
<meta charset="utf-8">
<title>Dwelvano Business Card</title>
<link rel="stylesheet" href="https://fonts.googleapis.com/css2?family=Montserrat:wght@400;600;800&family=Lato:wght@400&display=swap">
<style>
  :root {
    --stage: #1d1d1d;
    --card: #000000;
    --white: #ffffff;
    --teal: #0fb3c7;
    --rule: #e8e8e8;
  }
  * { box-sizing: border-box; margin: 0; padding: 0; }
  html, body { width: 1200px; height: 1059px; overflow: hidden; }
  body { background: var(--stage); position: relative; font-family: "Lato", sans-serif; color: var(--white); }

  .card {
    position: absolute;
    background: var(--card);
    border-radius: 28px;
    box-shadow: 0 14px 34px rgba(0,0,0,0.55);
  }
  .card-front { left: 254px; top: 85px; width: 692px; height: 396px; }
  .card-back  { left: 254px; top: 547px; width: 705px; height: 403px; }

  .wordmark {
    position: absolute;
    display: flex;
    align-items: center;
    font-family: "Montserrat", sans-serif;
    font-weight: 800;
    color: var(--white);
    letter-spacing: -0.5px;
    line-height: 1;
  }
  .wordmark .mark-square { background: var(--teal); border-radius: 3px; }
  .card-front .wordmark { right: 32px; top: 60px; font-size: 52px; gap: 12px; }
  .card-front .mark-square { width: 30px; height: 30px; }
  .card-back .wordmark { left: 50%; top: 50%; transform: translate(-50%, -50%); font-size: 80px; gap: 16px; }
  .card-back .mark-square { width: 44px; height: 44px; }

  .person-name {
    position: absolute; left: 33px; top: 208px;
    font-family: "Montserrat", sans-serif; font-weight: 600;
    font-size: 28px; line-height: 1.2; color: var(--teal); letter-spacing: 0.5px;
  }
  .person-title {
    position: absolute; left: 31px; top: 244px;
    font-family: "Montserrat", sans-serif; font-weight: 400;
    font-size: 18px; line-height: 1.2; color: var(--white);
  }
  .divider { position: absolute; left: 31px; top: 273px; width: 626px; height: 1.5px; background: var(--rule); }

  .contact-list { position: absolute; list-style: none; font-size: 18px; }
  .contact-list li { display: flex; align-items: center; height: 28px; }
  .contact-list svg { width: 18px; height: 18px; fill: var(--teal); flex: none; }
  .phones { left: 33px; top: 283px; }
  .phones li { gap: 10px; height: 29px; }
  .online { left: 221px; top: 285px; }
  .online li { gap: 14px; height: 26px; }

  .address {
    position: absolute; right: 32px; top: 290px;
    font-style: normal; text-align: right; font-size: 18px; line-height: 23px;
  }
</style>
</head>
<body>

<section class="card card-front" aria-label="Card front">
  <div class="wordmark"><span class="mark-square"></span><span class="brand-name">Dwelvano</span></div>

  <h1 class="person-name">JOHN DOE</h1>
  <p class="person-title">Owner</p>
  <div class="divider"></div>

  <ul class="contact-list phones">
    <li class="office">
      <svg viewBox="0 0 24 24" aria-hidden="true"><path d="M2 9c0-3 5-5 10-5s10 2 10 5v2h-5V8.5c-1.5-.6-3.3-.9-5-.9s-3.5.3-5 .9V11H2z"/><path d="M6 12l2-3h8l2 3v8H6z"/></svg>
      <span>(555) 201-4470</span>
    </li>
    <li class="cell">
      <svg viewBox="0 0 24 24" aria-hidden="true"><path d="M7 1h10a2 2 0 0 1 2 2v18a2 2 0 0 1-2 2H7a2 2 0 0 1-2-2V3a2 2 0 0 1 2-2zm0 3v14h10V4zm5 15.5a1.2 1.2 0 1 0 0 2.4 1.2 1.2 0 0 0 0-2.4z"/></svg>
      <span>(555) 201-4488</span>
    </li>
    <li class="fax">
      <svg viewBox="0 0 24 24" aria-hidden="true"><path d="M1 7h5v15H1zM8 3h10l3 3v16H8zm2 8v2h2v-2zm4 0v2h2v-2zm-4 4v2h2v-2zm4 0v2h2v-2zm4-4v2h1v-2zm0 4v2h1v-2zM10 5v4h9V7l-2-2z"/></svg>
      <span>(555) 201-4495</span>
    </li>
  </ul>

  <ul class="contact-list online">
    <li class="email">
      <svg viewBox="0 0 24 24" aria-hidden="true"><path d="M2 5h20v2l-10 6L2 7z"/><path d="M2 9.3l10 6 10-6V19H2z"/></svg>
      <span>johndoe@dwelvano.com</span>
    </li>
    <li class="website">
      <svg viewBox="0 0 24 24" aria-hidden="true"><path d="M12 2a10 10 0 1 0 0 20 10 10 0 0 0 0-20zm0 2.2c1 0 2 .3 2.9.7l-1.4 1.6-2.3-.3-1 1.8 1.5 1.3-.6 1.6-2.6-.5-1.7 2 1.2 2.8 2.3.7.2 3.5a7.8 7.8 0 0 1-6-9.5L6.3 9l1.9-.4.8-2.2-1.8-.6A7.8 7.8 0 0 1 12 4.2zm5.6 2.4a7.8 7.8 0 0 1 1.5 9.5l-1.9-1.7.3-2.9-2.1-1.5.4-2.3z"/></svg>
      <span>www.dwelvano.com</span>
    </li>
  </ul>

  <address class="address">
    480 Cedar Avenue,<br>
    Suite 210, Marlow Bay,<br>
    FL 32999
  </address>
</section>

<section class="card card-back" aria-label="Card back">
  <div class="wordmark"><span class="mark-square"></span><span class="brand-name">Dwelvano</span></div>
</section>

</body>
</html>
```